****Business Card Design for Quarrystone Development. Design based around attached logo/company name

I’m looking for business card design for my company Quarrystone Development Group,LLC. Design should be professional, sharp and minimal. Outside of the attached logos, greyscale colors for remainder of cards. My thoughts are two-sided card with attached logo on one side and my info on the other but open to one-sided as well with right design.
Target Market(s)
Real estate professionals including banks, private investors, property owners, developers, commercial tenants like Brewlantern, Grovika or Tanquist’s.
Industry/Entity Type
Commercial real estate development and investments.
Contact Information for Business Card
Name, title, email, phone #’s, web address and physical address
Font styles to use
Other font styles liked:
- Helvetica, Garamond, etc
Colors
Designer to choose only greyscale colors for use in the design.
Requirements
Must have
- Attached logo first or second options.
Nice to have
- Two sided card with logo on one side. Attached Logo/company name can be laid out any way that flows as long as it’s legible.name
Should not have
- No loud colors. ***Please do not include logo, I have removed the company design with a logo image.

```html
<!DOCTYPE html>
<html lang="en">
<head>
<meta charset="utf-8">
<title>Quarrystone Development Group, LLC — Business Card</title>
<link href="https://fonts.googleapis.com/css2?family=EB+Garamond:wght@400;700&family=Arimo:wght@400&display=swap" rel="stylesheet">
<style>
  :root {
    --backdrop: #2e2e2e;
    --card: #ffffff;
    --slate: #5a6375;
    --ink-grey: #8a8a8a;
    --panel-text: #ffffff;
  }
  * { box-sizing: border-box; margin: 0; padding: 0; }
  html, body {
    width: 1200px; height: 901px; overflow: hidden;
    background: var(--backdrop);
  }
  .card {
    position: absolute; left: 100px; top: 164px;
    width: 1000px; height: 572px;
    background: var(--card);
    box-shadow: 0 12px 30px rgba(0,0,0,0.45);
  }
  .brand-panel {
    position: absolute; left: 110px; top: 130px;
    width: 440px; height: 290px;
    background: var(--slate);
    border-radius: 20px;
    display: flex; align-items: center; justify-content: center;
    padding: 0 30px;
  }
  .brand-name {
    font-family: "EB Garamond", Garamond, serif;
    font-weight: 400;
    color: var(--panel-text);
    text-transform: uppercase;
    text-align: center;
    font-size: 30px;
    line-height: 1.25;
    letter-spacing: 2px;
  }
  .contact {
    position: absolute; left: 590px; top: 185px;
    font-family: "Arimo", Helvetica, Arial, sans-serif;
    color: var(--ink-grey);
  }
  .person-name {
    font-family: "EB Garamond", Garamond, serif;
    font-weight: 700;
    font-size: 30px;
    letter-spacing: 1px;
    color: var(--slate);
    text-transform: uppercase;
    line-height: 1.1;
  }
  .person-title { font-size: 23px; line-height: 1.2; margin-bottom: 14px; }
  .address { font-size: 22px; line-height: 1.3; margin-bottom: 14px; }
  .contact-line {
    display: flex; align-items: center; gap: 10px;
    font-size: 22px; line-height: 1.55;
  }
  .contact-line svg { width: 18px; height: 18px; fill: var(--slate); flex: none; }
</style>
</head>
<body>
  <div class="card">
    <div class="brand-panel">
      <p class="brand-name">Quarrystone<br>Development Group, LLC</p>
    </div>
    <div class="contact">
      <p class="person-name">Declan Whitmore</p>
      <p class="person-title">Founder/CEO</p>
      <p class="address">2190 Harbor Ridge Road<br>Lakeview AB 5120</p>
      <p class="contact-line">
        <svg viewBox="0 0 24 24" aria-hidden="true"><path d="M6.6 10.8a15.1 15.1 0 0 0 6.6 6.6l2.2-2.2c.3-.3.7-.4 1-.2 1.1.4 2.3.6 3.6.6.6 0 1 .4 1 1V20c0 .6-.4 1-1 1A17 17 0 0 1 3 4c0-.6.4-1 1-1h3.5c.6 0 1 .4 1 1 0 1.3.2 2.5.6 3.6.1.3 0 .7-.2 1z"/></svg>
        (555)-214-3390
      </p>
      <p class="contact-line">
        <svg viewBox="0 0 24 24" aria-hidden="true"><path d="M2 5h20v14H2z M2 5l10 8 10-8" fill="none" stroke="currentColor"/><path d="M2 5h20v1.5l-10 7.5L2 6.5z M2 8.5l10 7.5 10-7.5V19H2z"/></svg>
        info@quarrystonedevelopment.com
      </p>
      <p class="contact-line">
        <svg viewBox="0 0 24 24" aria-hidden="true"><circle cx="12" cy="12" r="9" fill="none" stroke="#5a6375" stroke-width="2"/><path d="M3 12h18M12 3c3 3 3 15 0 18M12 3c-3 3-3 15 0 18" fill="none" stroke="#5a6375" stroke-width="1.6"/></svg>
        www.quarrystonedevelopment.com
      </p>
    </div>
  </div>
</body>
</html>
```